Marwick Law Letterhead

We need a new letterhead design for a Law Firm. The address for the law firm is 1475 Calloway Street, Suite 210, Houston, Texas 77041. Phone Number: 832-361-9027; Fax Number: 832-614-7359. The logo is uploaded to the project.

```html
<!DOCTYPE html>
<html lang="en">
<head>
<meta charset="utf-8">
<title>Marwick Law Letterhead</title>
<link href="https://fonts.googleapis.com/css2?family=Figtree:wght@400;500;700&display=swap" rel="stylesheet">
<style>
  :root{
    --bg:#e8e8e8;
    --paper:#ffffff;
    --navy:#1f3366;
    --red:#c8161e;
    --red-deep:#7a0a10;
    --ink:#222222;
    --ink-soft:#333333;
  }
  *{margin:0;padding:0;box-sizing:border-box}
  html,body{width:1154px;height:1200px;overflow:hidden;background:var(--bg)}
  body{font-family:"Figtree",Arial,sans-serif;color:var(--ink)}
  .letterhead{position:absolute;left:147px;top:0;width:859px;height:1200px;background:var(--paper);overflow:hidden}
  .brand{position:absolute;left:34px;top:108px;display:flex;align-items:center;gap:12px}
  .brand-mark{width:28px;height:28px;background:var(--navy);border-radius:50%}
  .brand-name{font-size:34px;font-weight:700;color:var(--navy);letter-spacing:.5px;line-height:40px}
  .contact{position:absolute;left:630px;top:89px;height:104px;border-left:2px solid var(--red);padding-left:21px;font-size:14.5px;line-height:18.5px;color:var(--ink);font-style:normal}
  .contact-line{display:flex;align-items:center;gap:10px}
  .contact-line.first{margin-top:9px}
  .contact-line svg{width:12px;height:12px;flex:none}
  .recipient{position:absolute;left:31px;top:301px;font-size:14.5px;line-height:21.4px}
  .letter-body{position:absolute;left:34px;top:393px;width:795px;font-size:15.4px;line-height:21.4px;color:var(--ink-soft);text-align:justify;hyphens:auto}
  .letter-body p{margin-bottom:21.4px}
  .closing{position:absolute;left:31px;top:900px;font-size:17.5px;line-height:22px}
  .signature{position:absolute;left:31px;top:928px;width:95px;height:30px;background:linear-gradient(90deg,#e4e4e4,#f2f2f2);border-radius:4px}
  .footer-band{position:absolute;left:0;bottom:0;width:859px;height:118px;background:linear-gradient(180deg,var(--red) 0%,var(--red-deep) 100%)}
</style>
</head>
<body>
<main class="letterhead">
  <header>
    <div class="brand">
      <span class="brand-mark"></span>
      <span class="brand-name">Marwick Law</span>
    </div>
    <address class="contact">
      <div class="contact-address">1475 Calloway Street,<br>Suite 210, Houston,<br>Texas 77041</div>
      <div class="contact-line first">
        <svg viewBox="0 0 24 24" aria-hidden="true"><path fill="#c8161e" d="M6.6 10.8a15.1 15.1 0 0 0 6.6 6.6l2.2-2.2a1 1 0 0 1 1-.25 11.4 11.4 0 0 0 3.6.57 1 1 0 0 1 1 1V20a1 1 0 0 1-1 1A17 17 0 0 1 3 4a1 1 0 0 1 1-1h3.5a1 1 0 0 1 1 1c0 1.25.2 2.45.57 3.6a1 1 0 0 1-.25 1z"/></svg>
        <span>832-361-9027</span>
      </div>
      <div class="contact-line">
        <svg viewBox="0 0 24 24" aria-hidden="true"><path fill="#c8161e" d="M6 2h12v5H6zM4 8h16a2 2 0 0 1 2 2v6h-4v6H6v-6H2v-6a2 2 0 0 1 2-2zm4 8v4h8v-4z"/></svg>
        <span>832-614-7359</span>
      </div>
    </address>
  </header>

  <section class="recipient">
    Mr/s<br>First Name and Last Name<br>Company Name<br>Address
  </section>

  <section class="letter-body" lang="la">
    <p>Lorem ipsum dolor sit amet,consectetur adipiscing sed do eiusmod tempor incididunt laboreet dolore magna aliqua.Ut enim ad minim.veniam, quis nostrud exercitation ullamco laboris nisi ut aliquip exea commodo consequat.Lorem ipsum dolor sit amet,consectetur adipiscing sed do eiusmod tempor incididunt.labore et dolore magna aliqua. Ut enim</p>
    <p>Lorem ipsum dolor sit amet, consectetur adipiscing sed do eiusmod tempor incididunt labore et dolore magna aliqua. Ut enim ad minim veniam, quis nostrud exercitation ullamco laboris nisi ut aliquip exea commodo consequat.Duis aute irure dolor in reprehenderit in voluptate velit esse cillum irure dolor in reprehenderit in voluptate velit esse irure</p>
    <p>Lorem ipsum dolor sit amet, consectetur adipiscing sed do eiusmod tempor incididunt labore et dolore magna aliqua. consequat. Duis aute irure dolor in.reprehenderit in voluptate velit esse cillum dolore eu fugiat nulla pariatur. Excepteur sint occaecat cupidatat non proident, sunt in culpa qui officia deserunt mollit,</p>
    <p>Lorem ipsum dolor sit amet, consectetur adipiscing sed do eiusmod tempor incididunt labore et dolore magna aliqua. Ut enim Lorem ipsum dolor sit amet, consectetur adipiscing sed do eiusmod tempor incididunt labore et dolore magna aliqua. Ut enim Lorem ipsum aliqua.ipsum</p>
    <p>Lorem ipsum dolor sit amet, consectetur adipiscing sed do eiusmod tempor incididunt labore et dolore magna aliqua. Ut enim ad minim veniam, quis nostrud exercitation ullamco laboris nisi ut aliquip exea commodo consequat.Duis aute irure dolor in reprehenderit in voluptate velit esse cillum irure dolor in reprehenderit in voluptate velit esse irure</p>
  </section>

  <div class="closing">Regards</div>
  <div class="signature" role="img" aria-label="Handwritten signature"></div>

  <div class="footer-band" role="img" aria-label="Decorative red footer band with navy edge"></div>
</main>
</body>
</html>
```